first fantastic look and impression

We are looking for a concept for letterhead, business card, emailfooter and template for invoices or offers for our company in the consultation business.
The dancer is a symbol who we are: it looks simple, but there is a lot of hard work and many years of training in this movement. The look is also what we want: elegant, modern, strong, with a touch of extravaganza
Target Market(s)
Hotelbusiness , Consulting
Font styles to use
Sans Serif
Other font styles liked:
- please give us a option we are open
Requirements
Must have
- We are not typical consultants but sparring partners and coaches for the hotel and that should also be expressed in the design. Maybe there is an icon that supports the whole thing. We are more modern and bolder than our industry colleagues.
we are modern, fresh, agile, fast
Nice to have
- a icon

```html
<!DOCTYPE html>
<html lang="en">
<head>
<meta charset="UTF-8">
<title>Business Card – Front and Back</title>
<link rel="stylesheet" href="https://fonts.googleapis.com/css2?family=Roboto:wght@400&family=Khand:wght@600&display=swap">
<style>
  :root {
    --backdrop: #6a6a6a;
    --card-dark: #161616;
    --card-light: #f1f1f1;
    --ink: #111111;
    --ink-soft: #222222;
    --band: #0c0c0c;
    --band-text: #e8e8e8;
    --art-tone-a: #2a2a2a;
    --art-tone-b: #1b1b1b;
  }
  * { margin: 0; padding: 0; box-sizing: border-box; }
  html, body {
    width: 1200px; height: 1138px; overflow: hidden;
    background: var(--backdrop);
  }
  .canvas { position: relative; width: 1200px; height: 1138px; }

  .card {
    position: absolute;
    width: 620px; height: 374px;
    border-radius: 16px;
    overflow: hidden;
  }
  .card--front { left: 274px; top: 186px; background: var(--card-dark); }
  .card--back  { left: 276px; top: 608px; background: var(--card-light); }

  .dancer-art {
    position: absolute;
    left: 162px; top: 58px; width: 302px; height: 280px;
    border-radius: 46% 54% 40% 60% / 50% 40% 60% 50%;
    background: radial-gradient(ellipse at 55% 45%, var(--art-tone-a) 0%, var(--art-tone-b) 70%, var(--card-dark) 100%);
  }

  .brand-name {
    position: absolute;
    left: 0; width: 372px; top: 146px;
    text-align: center;
    font-family: "Roboto", sans-serif;
    font-weight: 400;
    font-size: 34px;
    letter-spacing: 1px;
    color: var(--ink);
  }

  .contact-block {
    position: absolute; left: 360px; top: 68px;
    font-family: "Roboto", sans-serif; color: var(--ink-soft);
  }
  .person-name {
    font-family: "Khand", sans-serif; font-weight: 600;
    font-size: 27px; line-height: 1; color: var(--ink);
  }
  .person-role { font-size: 16px; margin-top: 6px; }
  .contact-list { list-style: none; margin-top: 22px; }
  .contact-list li {
    display: flex; align-items: center;
    font-size: 16px; height: 24px;
  }
  .contact-list svg { width: 14px; height: 14px; margin-right: 18px; fill: var(--ink); }
  .address { font-size: 16px; line-height: 23px; margin-top: 6px; padding-left: 4px; }

  .tagline-band {
    position: absolute; left: 0; bottom: 0; width: 620px; height: 46px;
  }
  .tagline-band svg { position: absolute; inset: 0; }
  .tagline {
    position: absolute; left: 360px; top: 12px;
    font-family: "Roboto", sans-serif; font-size: 16px; color: var(--band-text);
  }
</style>
</head>
<body>
<div class="canvas">

  <section class="card card--front">
    <div class="dancer-art" role="img" aria-label="Line illustration of a leaping dancer holding a flowing veil, blind-embossed black on black"></div>
  </section>

  <section class="card card--back">
    <div class="brand-name">Veyra Coaching</div>

    <div class="contact-block">
      <div class="person-name">John Doe Smith</div>
      <div class="person-role">Managing Director</div>
      <ul class="contact-list">
        <li>
          <svg viewBox="0 0 16 16" aria-hidden="true"><path d="M2 6c0-2 2-3 6-3s6 1 6 3v1h-3V5.5H5V7H2zM4 8h8l2 5H2z"/></svg>
          828-111-1111
        </li>
        <li>
          <svg viewBox="0 0 16 16" aria-hidden="true"><path d="M1 3h14v10H1zM2.5 4.5v.4L8 9l5.5-4.1v-.4zM2.5 6.8v4.7h11V6.8L8 10.9z"/></svg>
          john@yourwebsite.com
        </li>
        <li>
          <svg viewBox="0 0 16 16" aria-hidden="true"><path d="M8 1a7 7 0 1 0 0 14A7 7 0 0 0 8 1zm0 1.4c.8 0 1.7 1.4 2 3.6H6c.3-2.2 1.2-3.6 2-3.6zM2.5 7.2h2.4v1.6H2.5zm3.6 0h3.8v1.6H6.1zm5 0h2.4v1.6h-2.4zM6 10h4c-.3 2.2-1.2 3.6-2 3.6S6.3 12.2 6 10z"/></svg>
          www.yourwebsite.com
        </li>
      </ul>
      <p class="address">234 Anywhere St., Any City,<br>Any Town, US 123456</p>
    </div>

    <div class="tagline-band">
      <svg viewBox="0 0 620 46" width="620" height="46" aria-hidden="true">
        <path d="M276 46 L292 6 Q295 0 302 0 L620 0 L620 46 Z" fill="var(--band)"/>
      </svg>
      <span class="tagline">Elegant and Fasion</span>
    </div>
  </section>

</div>
</body>
</html>
```